Architectural, Engineering and Design Build

Tovandex4.com
Veteran Disabled Certified company is doing business in Architecture, Engineer and Design build - look simialr websites and come up with design follow following website
https://hollis-darnet.example/
https://www.venlorcogroup.example/
https://www.pembrisgc.example/contract-vehicles/service-disabled-veteran-owned-small-business-sdvosb/
https://www.corbelnetlink.example/about/sdvosb/

Target Market(s)

US - Defense and Federal Government

Industry/Entity Type

Colors
0054AA
0677BA
7BADD7
CADEEF
E8F1F8

Requirements
Must have
• Army, American patriotism , Buildings, construction, architecture, engineering
Nice to have
• I need to attract federal government agencies and Defense

```html
<!DOCTYPE html>
<html lang="en">
<head>
<meta charset="utf-8">
<title>Tovandex4 — Architecture, Engineering &amp; Design Build</title>
<link href="https://fonts.googleapis.com/css2?family=Cabin:wght@500;600;700&family=Lato:wght@400;700&display=swap" rel="stylesheet">
<style>
:root{
  --blue:#0054AA;
  --blue-mid:#0677BA;
  --blue-soft:#7BADD7;
  --blue-pale:#CADEEF;
  --blue-ice:#E8F1F8;
  --ink:#2b2b2b;
  --text:#444;
  --muted:#666;
  --dark:#3a3a3a;
  --light:#f2f2f2;
  --white:#fff;
  --star:#f5c400;
}
*{box-sizing:border-box;margin:0;padding:0}
html,body{width:1200px;height:3436px;overflow:hidden;background:var(--white)}
body{font-family:"Lato",sans-serif;color:var(--text)}
.page{position:relative;width:1200px;height:3436px;overflow:hidden}
.abs{position:absolute}
h1,h2,h3{font-family:"Cabin",sans-serif}

/* header */
.site-header{position:absolute;left:0;top:0;width:1200px;height:135px;background:var(--white)}
.brand{position:absolute;left:50px;top:36px;font-size:50px;color:var(--ink);letter-spacing:1px}
.nav{position:absolute;left:588px;top:60px;display:flex;gap:25px;font-size:17px;color:var(--ink)}
.btn-outline{position:absolute;border:2px solid var(--blue);color:var(--blue);display:flex;align-items:center;justify-content:center;font-size:17px;background:transparent;border-radius:3px}

/* hero */
.hero{position:absolute;left:0;top:135px;width:1200px;height:587px;
  background:linear-gradient(180deg,#2c3a55 0%,#4a4a5a 35%,#6a5a4a 70%,#3f3a40 100%)}
.hero-overlay{position:absolute;inset:0;background:linear-gradient(90deg,rgba(20,30,60,.55),rgba(20,30,60,.15))}
.hero-title{position:absolute;left:71px;top:158px;font-size:48px;font-weight:700;line-height:58px;color:var(--white)}
.hero-sub{position:absolute;left:74px;top:290px;width:540px;font-size:22px;line-height:34px;color:var(--white)}
.contact-card{position:absolute;left:772px;top:106px;width:359px;height:409px;background:var(--white);border-radius:8px}
.contact-card h3{position:absolute;top:36px;width:100%;text-align:center;font-size:20px;font-weight:600;color:var(--ink)}
.field{position:absolute;left:50px;width:263px;height:37px;border:1px solid #ccc;font-size:11px;color:var(--muted);padding:12px 16px}
.submit{position:absolute;left:52px;top:337px;width:262px;height:37px;background:var(--blue);color:var(--white);font-weight:700;font-size:16px;display:flex;align-items:center;justify-content:center}

/* intro */
.intro-title{position:absolute;left:0;top:772px;width:1200px;text-align:center;font-size:36px;line-height:49px;font-weight:700;color:var(--ink)}
.service-card{position:absolute;top:998px;width:510px;height:324px;background:var(--white);box-shadow:0 0 12px rgba(0,0,0,.08)}
.service-photo{position:absolute;left:0;top:0;width:228px;height:324px}
.service-body{position:absolute;left:258px;top:34px;width:215px}
.service-body h3{margin-top:20px;font-size:18px;font-weight:600;color:var(--ink)}
.service-body p{margin-top:16px;font-size:13px;line-height:21px;color:var(--text)}
.btn-small{display:inline-flex;margin-top:24px;background:var(--blue);color:var(--white);font-size:12px;font-weight:700;padding:11px 16px}

/* projects */
.projects{position:absolute;left:0;top:1416px;width:1200px;height:456px;background:var(--dark);overflow:hidden}
.projects-watermark{position:absolute;left:44px;top:64px;font-family:"Cabin",sans-serif;font-weight:700;font-size:180px;letter-spacing:30px;color:transparent;-webkit-text-stroke:1px rgba(255,255,255,.06);line-height:1}
.eyebrow{position:absolute;left:52px;top:96px;font-family:"Cabin",sans-serif;font-size:20px;font-weight:600;color:var(--white);display:flex;align-items:center;gap:14px}
.eyebrow::before{content:"";width:24px;height:3px;background:var(--blue-mid)}
.projects-title{position:absolute;left:52px;top:126px;font-size:41px;line-height:60px;font-weight:700;color:var(--white)}
.projects-text{position:absolute;left:504px;top:136px;width:660px;font-size:16px;line-height:28px;color:#e6e6e6}
.project-tile{position:absolute;top:1733px;width:209px;height:265px}
.tile-caption{position:absolute;left:18px;bottom:22px;color:var(--white);font-family:"Cabin",sans-serif;font-size:13px;font-weight:700}
.tile-caption .tag{display:block;margin-top:12px;padding-left:10px;border-left:3px solid #e33}

.light-band{position:absolute;left:0;top:1872px;width:1200px;height:883px;background:var(--light)}
.t-eyebrow{position:absolute;left:0;top:2218px;width:1188px;text-align:center;font-family:"Cabin",sans-serif;font-size:23px;font-weight:600;color:var(--blue)}
.t-title{position:absolute;left:0;top:2264px;width:1196px;text-align:center;font-size:36px;font-weight:600;color:var(--ink)}
.t-title span{color:var(--blue)}
.testimonial{position:absolute;top:2402px;width:465px;height:236px;background:var(--white);box-shadow:0 2px 12px rgba(0,0,0,.06)}
.avatar{position:absolute;left:30px;top:30px;width:94px;height:94px;border-radius:50%}
.quote-text{position:absolute;left:154px;top:32px;width:275px;font-size:13px;line-height:23px;color:var(--muted)}
.person{position:absolute;left:154px;top:136px;font-family:"Cabin",sans-serif;font-size:18px;font-weight:600;color:var(--ink)}
.stars{position:absolute;left:154px;top:170px;font-size:14px;letter-spacing:2px;color:var(--star)}
.stars .off{color:#aaa}
.quote-mark{position:absolute;right:30px;top:154px}
.arrow-btn{position:absolute;width:50px;height:50px;border-radius:50%;background:var(--white);box-shadow:0 2px 8px rgba(0,0,0,.1);display:flex;align-items:center;justify-content:center}

/* cta */
.cta{position:absolute;left:0;top:2755px;width:1200px;height:335px;
  background:linear-gradient(180deg,#6b4a25 0%,#9a6a2c 35%,#4a3a30 70%,#2a2a2a 100%)}
.cta-overlay{position:absolute;inset:0;background:rgba(0,0,0,.25)}
.cta-title{position:absolute;left:0;top:66px;width:1222px;text-align:center;font-size:38px;line-height:55px;font-weight:700;color:var(--white)}
.btn-light{position:absolute;left:530px;top:206px;width:184px;height:55px;border:2px solid var(--white);color:var(--white);font-family:"Cabin",sans-serif;font-weight:600;font-size:21px;display:flex;align-items:center;justify-content:center}

/* footer */
.site-footer{position:absolute;left:0;top:3090px;width:1200px;height:346px;background:linear-gradient(180deg,#2e2e2e,#141414)}
.footer-nav{position:absolute;left:0;top:65px;width:1200px;display:flex;justify-content:center;gap:18px;font-size:16px;color:var(--white)}
.footer-nav .sep{color:#bbb}
.footer-brand{position:absolute;left:53px;top:142px;font-size:56px;color:#555;letter-spacing:1px}
.socials{position:absolute;left:661px;top:136px;display:flex;gap:18px}
.social{width:60px;height:60px;border-radius:50%;border:2px solid #bbb}
.copyright{position:absolute;left:0;top:292px;width:1210px;text-align:center;font-size:14px;color:#bbb}
</style>
</head>
<body>
<div class="page">

  <header class="site-header">
    <div class="brand">LOGO</div>
    <nav class="nav"><span>HOME</span><span>ABOUT</span><span>FEATURED</span><span>CONTACT</span></nav>
    <a class="btn-outline" style="left:986px;top:48px;width:166px;height:46px">GET STARTED</a>
  </header>

  <section class="hero" role="img" aria-label="Photo of the domed federal capitol building at dusk">
    <div class="hero-overlay"></div>
    <h1 class="hero-title">Service Disabled Veteran<br>Owned Small Business</h1>
    <p class="hero-sub">We’ll prepare a proposal and walk you through every step of the process.</p>
    <svg class="abs" style="left:545px;top:398px" width="185" height="40" viewBox="0 0 185 40">
      <path d="M2 4 C40 30 110 34 178 30" fill="none" stroke="#fff" stroke-width="1.6"/>
      <path d="M170 25 L179 30 L170 35" fill="none" stroke="#fff" stroke-width="1.6"/>
    </svg>
    <form class="contact-card">
      <h3>Contact Us</h3>
      <div class="field" style="top:88px">Name*</div>
      <div class="field" style="top:139px">Email*</div>
      <div class="field" style="top:190px">Subject*</div>
      <div class="field" style="top:241px;height:69px">Message</div>
      <div class="submit">SUBMIT</div>
    </form>
  </section>

  <h2 class="intro-title">Technology to take products from<br>an idea all the way to the end consumer.</h2>
  <a class="btn-outline" style="left:467px;top:898px;width:297px;height:45px;font-weight:700;font-size:19px">BOOK A CONSULTATION</a>

  <article class="service-card" style="left:50px">
    <div class="service-photo" role="img" aria-label="Photo of a glass pavilion beside a pond" style="background:linear-gradient(160deg,#b9c7d6,#5c6d72 55%,#3c4a44)"></div>
    <div class="service-body">
      <svg width="60" height="62" viewBox="0 0 60 62" fill="none" stroke="var(--blue)" stroke-width="2.2">
        <path d="M14 24 C14 10 46 10 46 24 Z"/><path d="M10 24 H50"/><path d="M30 10 V4"/>
        <path d="M18 28 C18 40 42 40 42 28"/><path d="M8 60 V50 C8 44 16 42 22 42 H38 C44 42 52 44 52 50 V60"/><path d="M24 42 L30 52 L36 42"/>
      </svg>
      <h3>Construction</h3>
      <p>Donec scelerisque dolor id nunc dictum, interdum gravida mauris rhoncus. Aliquam</p>
      <span class="btn-small">GET STARTED</span>
    </div>
  </article>

  <article class="service-card" style="left:641px">
    <div class="service-photo" role="img" aria-label="Photo of a glass office tower against blue sky" style="background:linear-gradient(160deg,#9cc3e6,#2f5f8a 50%,#163247)"></div>
    <div class="service-body">
      <svg width="70" height="62" viewBox="0 0 70 62" fill="none" stroke="var(--blue)" stroke-width="2.2">
        <path d="M4 14 H60 V58 H4 Z"/><path d="M4 14 C4 8 12 8 12 14 V50 C12 56 4 56 4 50"/>
        <circle cx="44" cy="8" r="4"/><path d="M42 12 L32 46"/><path d="M46 12 L56 46"/><path d="M36 32 H52"/>
      </svg>
      <h3>Architecture</h3>
      <p>Donec scelerisque dolor id nunc dictum, interdum gravida mauris rhoncus. Aliquam</p>
      <span class="btn-small">GET STARTED</span>
    </div>
  </article>

  <section class="projects">
    <div class="projects-watermark">PROJECTS</div>
    <div class="eyebrow">LATEST PROJECTS</div>
    <h2 class="projects-title">Let’s Explore Our<br>Recent Works</h2>
    <p class="projects-text">The right software solution by itself will not run your business. It takes a team to do that. In addition to selecting the best cloud solution on the market, it takes smart and dedicated people remaining essentially unchanged.</p>
  </section>
  <div class="light-band"></div>

  <div class="project-tile" style="left:245px;background:linear-gradient(180deg,#2f5a78,#5a5f8a 55%,#1e2038)" role="img" aria-label="Photo of a city skyline at night">
    <div class="tile-caption">Commercial &nbsp;Residential<span class="tag">Modern House</span></div>
  </div>
  <div class="project-tile" style="left:474px;background:linear-gradient(180deg,#2a6fc0,#4c8fd4 50%,#c7a56a 75%,#2e5a8a)" role="img" aria-label="Photo of a curved modern concert hall at twilight"></div>
  <div class="project-tile" style="left:710px;background:linear-gradient(180deg,#e6edf3,#c89a3a 45%,#3f6a5a 80%)" role="img" aria-label="Photo of a building under construction with a tower crane"></div>
  <div class="project-tile" style="left:940px;background:linear-gradient(160deg,#eeeeee,#c9cccf 60%,#9ea4aa)" role="img" aria-label="Photo of a white architectural scale model on blueprints"></div>

  <a class="btn-outline" style="left:546px;top:2039px;width:166px;height:45px;font-weight:700;font-size:17px">VIEW MORE</a>

  <div class="t-eyebrow">TESTIMONIALS</div>
  <h2 class="t-title">Words From <span>Clients</span></h2>

  <div class="arrow-btn" style="left:51px;top:2496px"><svg width="12" height="14" viewBox="0 0 12 14"><path d="M8 2 L3 7 L8 12" fill="none" stroke="#333" stroke-width="1.5"/></svg></div>
  <div class="arrow-btn" style="left:1101px;top:2492px"><svg width="12" height="14" viewBox="0 0 12 14"><path d="M4 2 L9 7 L4 12" fill="none" stroke="#333" stroke-width="1.5"/></svg></div>

  <article class="testimonial" style="left:121px">
    <div class="avatar" role="img" aria-label="Portrait of client Dorin Vasquell" style="background:linear-gradient(160deg,#c8ccd0,#7a6a5c)"></div>
    <p class="quote-text">when an unknown printer took a galley of type and scrambled it to make a type not only five centurie when an unknown printer took a galley of type</p>
    <div class="person">Dorin Vasquell</div>
    <div class="stars">★★★★<span class="off">★</span></div>
    <svg class="quote-mark" width="42" height="34" viewBox="0 0 42 34" fill="var(--blue-soft)"><path d="M2 0 H18 V18 C18 28 12 33 4 34 L3 29 C8 27 10 24 10 20 H2 Z M24 0 H40 V18 C40 28 34 33 26 34 L25 29 C30 27 32 24 32 20 H24 Z"/></svg>
  </article>

  <article class="testimonial" style="left:621px">
    <div class="avatar" role="img" aria-label="Portrait of client Tamsin Orley" style="background:linear-gradient(160deg,#3a7fa8,#2b3a48)"></div>
    <p class="quote-text">when an unknown printer took a galley of type and scrambled it to make a type not only five centurie when an unknown printer took a galley of type</p>
    <div class="person">Tamsin Orley</div>
    <div class="stars">★★★★<span class="off">★</span></div>
    <svg class="quote-mark" width="42" height="34" viewBox="0 0 42 34" fill="var(--blue-soft)"><path d="M2 0 H18 V18 C18 28 12 33 4 34 L3 29 C8 27 10 24 10 20 H2 Z M24 0 H40 V18 C40 28 34 33 26 34 L25 29 C30 27 32 24 32 20 H24 Z"/></svg>
  </article>

  <section class="cta" role="img" aria-label="Photo of a city skyline at golden hour">
    <div class="cta-overlay"></div>
    <h2 class="cta-title">Please feel free to contact us if you have any<br>question or queries</h2>
    <a class="btn-light">CONTACT US</a>
  </section>

  <footer class="site-footer">
    <nav class="footer-nav">
      <span>Home</span><span class="sep">|</span><span>Services</span><span class="sep">|</span><span>Services</span><span class="sep">|</span><span>Contact</span><span class="sep">|</span><span>About</span><span class="sep">|</span><span>Blog</span>
    </nav>
    <div class="footer-brand">LOGO</div>
    <div class="socials">
      <span class="social" aria-label="Social profile"></span>
      <span class="social" aria-label="Social profile"></span>
      <span class="social" aria-label="Social profile"></span>
      <span class="social" aria-label="Social profile"></span>
      <span class="social" aria-label="Social profile"></span>
    </div>
    <p class="copyright">Copyright © 2024. All Rights Reserved.</p>
  </footer>

</div>
</body>
</html>
```